A5 Flyer for Financial Services Business

I am after a re-design of our business flyer to fit in with our new branding style and logo colour scheme. Wanting something with a bit of designer flair that I could not create myself. I have included the flyer which I created which lacks style so dazzle me.

I want to use the same content.

Text for main body of flyer is

Are you a small business owner, tradie or TRPQ Service Provider struggling to stay on top of your bookkeeping and compliance obligations? If so we would love to help you get back on track and take control of your business finances so that you can make informed business decisions and focus on what you do best.

We have over 20 years industry experience and, as a small business ourselves, we are able to offer our clients a personal bookkeeping solution tailored to meet the needs of your business.

Accounts Payable | Accounts Receivable
Customer Invoicing
Bank and Credit Card Reconciliations
Payroll | Superannuation | Payroll Tax
Business Activity | Instalment Activity Statements
Regular Financial Reports
Vantly and Brimfolk Set-Up and Training

```html
<!DOCTYPE html>
<html lang="en">
<head>
<meta charset="utf-8">
<title>Even Keel Financial Services – Bookkeeping Flyer</title>
<link rel="stylesheet" href="https://fonts.googleapis.com/css2?family=Montserrat:wght@500;600;700;800&family=Open+Sans:wght@400;600&display=swap">
<style>
  :root {
    --teal: #17a094;
    --teal-light: #4cc0b4;
    --teal-deep: #0f7f76;
    --navy: #1c3f5a;
    --ink: #333a40;
    --paper: #ffffff;
    --backdrop: #8a8a8a;
    --photo-a: #d9d9d9;
    --photo-b: #6e6e6e;
  }
  * { box-sizing: border-box; margin: 0; padding: 0; }
  html, body { width: 960px; height: 1200px; overflow: hidden; }
  body { background: var(--backdrop); font-family: "Open Sans", Arial, sans-serif; color: var(--ink); }

  .flyer {
    position: absolute; left: 70px; top: 20px;
    width: 820px; height: 1160px;
    background: var(--paper); overflow: hidden;
    box-shadow: 0 10px 30px rgba(0,0,0,.3);
  }
  .hero-art { position: absolute; left: 0; top: 0; width: 820px; height: 600px; }

  .brand { position: absolute; left: 34px; top: 40px; display: flex; align-items: center; gap: 10px; }
  .brand-mark { width: 26px; height: 26px; background: var(--navy); }
  .brand-name { font-family: "Montserrat", Arial, sans-serif; font-weight: 600; font-size: 17px; color: var(--navy); letter-spacing: .5px; line-height: 1.15; }

  .headline { position: absolute; left: 34px; top: 228px; color: var(--paper); font-family: "Montserrat", Arial, sans-serif; }
  .headline-top { font-size: 38px; font-weight: 700; letter-spacing: 1px; line-height: 1; }
  .headline-main { font-size: 64px; font-weight: 800; letter-spacing: 1px; line-height: 1.05; }
  .headline-sub { font-size: 18px; font-weight: 500; letter-spacing: 3px; }

  .credentials {
    position: absolute; left: 0; top: 380px; width: 300px; padding: 10px 16px 10px 34px;
    border: 2px solid var(--paper); border-left: none; border-radius: 0 10px 10px 0;
    color: var(--paper); font-size: 20px; line-height: 1.4;
  }

  .intro { position: absolute; left: 34px; top: 600px; width: 360px; font-size: 15.5px; line-height: 1.42; text-align: justify; }
  .intro p + p { margin-top: 22px; }

  .services { position: absolute; left: 410px; top: 598px; width: 390px; }
  .services-title { font-family: "Montserrat", Arial, sans-serif; font-size: 26px; font-weight: 600; color: var(--navy); margin-bottom: 12px; }
  .service-list { list-style: none; border-left: 3px dotted var(--teal); margin-left: 6px; }
  .service-list li { position: relative; padding-left: 22px; font-size: 16px; line-height: 1.3; margin-bottom: 15px; }
  .service-list li::before {
    content: ""; position: absolute; left: -10px; top: 4px; width: 14px; height: 14px;
    border-radius: 50%; background: var(--teal);
  }

  .contact { position: absolute; right: 0; top: 990px; width: 320px; }
  .contact-label { text-align: right; padding-right: 20px; font-family: "Montserrat", Arial, sans-serif; font-size: 15px; font-weight: 700; color: var(--teal); }
  .contact-box {
    display: flex; align-items: center; gap: 16px; height: 62px; padding-left: 24px;
    border: 3px solid var(--teal); border-right: none; border-radius: 16px 0 0 0;
  }
  .contact-phone { font-family: "Montserrat", Arial, sans-serif; font-size: 32px; font-weight: 700; color: var(--teal); }

  .website { position: absolute; left: 0; right: 0; top: 1104px; text-align: center; font-size: 19px; color: var(--teal); font-weight: 600; }
</style>
</head>
<body>
  <main class="flyer">
    <svg class="hero-art" viewBox="0 0 820 600">
      <defs>
        <linearGradient id="photoTone" x1="0" y1="0" x2="0" y2="1">
          <stop offset="0" stop-color="var(--photo-a)"/>
          <stop offset="1" stop-color="var(--photo-b)"/>
        </linearGradient>
      </defs>
      <path fill="var(--teal-light)" d="M420,150 C520,110 600,70 700,90 C760,100 800,120 820,110 L820,300 L420,300 Z"/>
      <path fill="var(--teal)" d="M0,200 C120,182 250,196 360,176 C480,152 560,100 700,118 C760,126 800,146 820,138 L820,520 C760,540 700,502 620,530 C540,558 470,520 400,546 C330,572 260,522 180,540 C100,558 50,530 0,546 Z"/>
      <path fill="var(--teal-deep)" opacity=".35" d="M0,546 C50,530 100,558 180,540 C260,522 330,572 400,546 L400,560 C330,585 260,535 180,555 C100,572 50,545 0,560 Z"/>
      <g role="img" aria-label="Photo of a smiling businesswoman holding a calculator">
        <rect x="475" y="150" width="330" height="330" rx="50" transform="rotate(45 640 315)" fill="url(#photoTone)" stroke="var(--paper)" stroke-width="8"/>
      </g>
    </svg>

    <div class="brand">
      <span class="brand-mark"></span>
      <span class="brand-name">EVEN KEEL<br>Financial Services</span>
    </div>

    <h1 class="headline">
      <div class="headline-top">BOOKKEEPING</div>
      <div class="headline-main">TAILORED</div>
      <div class="headline-sub">TO YOUR BUSINESS NEEDS</div>
    </h1>

    <div class="credentials">Vantly Certified Advisor<br>Brimfolk Pro Advisor</div>

    <section class="intro">
      <p>Are you a small business owner, tradie or TRPQ Service Provider struggling to stay on top of your bookkeeping and compliance obligations? If so we would love to help you get back on track and take control of your business finances so that you can make informed business decisions and focus on what you do best.</p>
      <p>We have over 20 years industry experience and, as a small business ourselves, we are able to offer our clients a personal bookkeeping solution tailored to meet the needs of your business.</p>
    </section>

    <section class="services">
      <h2 class="services-title">SERVICES WE PROVIDE</h2>
      <ul class="service-list">
        <li>Accounts Payable | Accounts Receivable</li>
        <li>Customer Invoicing</li>
        <li>Bank and Credit Card Reconciliations</li>
        <li>Business Activity | Instalment Activity Statements</li>
        <li>Payroll | Superannuation | Payroll Tax</li>
        <li>Regular Financial Reports</li>
        <li>Vantly and Brimfolk Set-Up and Training</li>
      </ul>
    </section>

    <section class="contact">
      <div class="contact-label">FOR MORE INFO</div>
      <div class="contact-box">
        <svg width="30" height="30" viewBox="0 0 24 24" aria-hidden="true">
          <path fill="var(--teal)" d="M6.6 10.8a15.1 15.1 0 0 0 6.6 6.6l2.2-2.2a1 1 0 0 1 1-.25 11.4 11.4 0 0 0 3.6.57 1 1 0 0 1 1 1V20a1 1 0 0 1-1 1A17 17 0 0 1 3 4a1 1 0 0 1 1-1h3.5a1 1 0 0 1 1 1c0 1.25.2 2.45.57 3.57a1 1 0 0 1-.25 1z"/>
        </svg>
        <span class="contact-phone">0400 123 456</span>
      </div>
    </section>

    <div class="website">www.evenkeelfinancialservices.com.au</div>
  </main>
</body>
</html>
```